New Business Card Design Project LORVANTI-Italy

we are LORVANTI-Italy
our company in the market for 3 years we are luxury cosmetic company and its about time for a facelift :)
i will like to have elegant luxurious and unique business card
that will give the person that get it a unique, luxurious and elegant impression
I'm VERY OPEN FOR NEW IDEAS , even duo i add a few files of things that i see on line and i like them

i add my logo as well
my website is LORVANTI.COM
(if you would like to see the main style that we have)

Target Market(s)

adult that have money :)

Industry/Entity Type

Business

Contact Information for Business Card

Name - Dario Lorvanti
Position - CEO and CO Founder
address - 4817 E Halvern
telephone - 555-384-1926
email - dario@lorvanti.com
fax - 555-384-1926
website - LORVANTI.COM

Colors
000000
959595
fbee3e
ffffff

Requirements
Must have
• big logo in GOLD color
• elegant look
• impressive
Nice to have
• not must but maybe classy pattern background
• not must but maybe emblem
• maybe clear plastic business card
Should not have
• colors
• images

```html
<!DOCTYPE html>
<html lang="en">
<head>
<meta charset="utf-8">
<title>LORVANTI Business Card</title>
<link rel="stylesheet" href="https://fonts.googleapis.com/css2?family=Roboto:wght@400;500;700&display=swap">
<style>
  :root {
    --backdrop: #2a2a2a;
    --card: #161616;
    --gold: #d9b23c;
    --gold-bright: #fbee3e;
    --silver: #959595;
    --silver-light: #d4d4d4;
    --white: #ffffff;
  }
  * { margin: 0; padding: 0; box-sizing: border-box; }
  html, body {
    width: 1200px;
    height: 900px;
    overflow: hidden;
    background: var(--backdrop);
    font-family: "Roboto", Arial, sans-serif;
  }
  .sheet {
    position: relative;
    width: 1200px;
    height: 900px;
  }
  .card {
    position: absolute;
    left: 285px;
    width: 630px;
    height: 360px;
    background: var(--card);
    box-shadow: 0 10px 30px rgba(0,0,0,0.45);
  }
  .card--front { top: 60px; }
  .card--back { top: 480px; }

  .brand {
    position: absolute;
    left: 0;
    right: 0;
    top: 110px;
    display: flex;
    flex-direction: column;
    align-items: center;
    gap: 22px;
  }
  .brand__mark {
    width: 76px;
    height: 76px;
    border-radius: 50%;
    background: var(--gold);
  }
  .brand__name {
    font-size: 44px;
    font-weight: 500;
    letter-spacing: 2px;
    color: var(--gold);
  }

  .person {
    position: absolute;
    left: 60px;
    top: 62px;
  }
  .person__name {
    font-size: 22px;
    font-weight: 700;
    color: var(--gold);
    letter-spacing: 0.5px;
    text-transform: uppercase;
  }
  .person__role {
    margin-top: 4px;
    font-size: 15px;
    color: var(--white);
  }

  .seal {
    position: absolute;
    right: 55px;
    top: 62px;
    width: 92px;
    height: 92px;
    border-radius: 50%;
    background: radial-gradient(circle at 35% 30%, var(--silver-light), var(--silver) 70%);
  }

  .contact {
    position: absolute;
    left: 60px;
    bottom: 60px;
    font-size: 15px;
    line-height: 1.6;
    color: var(--white);
  }
  .contact__label {
    color: var(--gold);
    font-weight: 700;
  }
  .contact__line--inline span + span { margin-left: 6px; }
</style>
</head>
<body>
<main class="sheet">
  <section class="card card--front" aria-label="Card front">
    <div class="brand">
      <div class="brand__mark"></div>
      <div class="brand__name">LORVANTI</div>
    </div>
  </section>

  <section class="card card--back" aria-label="Card back">
    <div class="person">
      <div class="person__name">Dario Lorvanti</div>
      <div class="person__role">CEO &amp; CO Founder</div>
    </div>
    <div class="seal"></div>
    <div class="contact">
      <div class="contact__line">4817 E Halvern</div>
      <div class="contact__line contact__line--inline">
        <span><span class="contact__label">P:</span> 555-384-1926</span>
        <span><span class="contact__label">F:</span> 555-384-1926</span>
        <span><span class="contact__label">E:</span> dario@lorvanti.com</span>
      </div>
      <div class="contact__line"><span class="contact__label">W:</span> LORVANTI.COM</div>
    </div>
  </section>
</main>
</body>
</html>
```